real esate business card with company logo and name

we need a business card design for a real esate company

The company name is Walsh & Brand Pty Ltd, and we have our logo designed and will upload. We want classic or moden feel. Black or white background. looks more textured. Should include folowinginformations
Owen Walsh and Lucy Brand
Sales Agents & Onsite Manager
p: 07 5948 2063
F: 07 5948 2174
M:0431 857 219
3/42 Marlow Crescent, FERNLEA QLD 4213

We want this business card looks professonal. Thank you in advance.

Industry/Entity Type

Real Estate Agent

Contact Information for Business Card

Owen Walsh and Lucy Brand
Onsite Manager & Sales Agents
p: 07 5948 2063
M:0431 857 219

Font styles to use
Serif

Colors
000000
fbfbfb
333333
959595

Requirements
Must have
• company logo and name, black or white back ground

```html
<!DOCTYPE html>
<html lang="en">
<head>
<meta charset="utf-8">
<title>Walsh &amp; Brand Pty Ltd — Business Card</title>
<link rel="stylesheet" href="https://fonts.googleapis.com/css2?family=Lato:wght@400;700&display=swap">
<style>
  :root {
    --stage: #3a3a3a;
    --card-light: #fbfbfb;
    --card-dark: #000000;
    --ink: #111111;
    --ink-soft: #333333;
    --mark-grey: #959595;
    --mark-light: #b8b8b8;
    --rule: #333333;
  }
  * { box-sizing: border-box; margin: 0; padding: 0; }
  html, body {
    width: 1200px;
    height: 1086px;
    overflow: hidden;
    background: var(--stage);
    font-family: "Lato", Arial, sans-serif;
  }
  .canvas { position: relative; width: 1200px; height: 1086px; }

  .card {
    position: absolute;
    left: 254px;
    width: 677px;
    height: 387px;
  }
  .card--front { top: 126px; background: var(--card-light); }
  .card--back  { top: 586px; background: var(--card-dark); }

  /* front: brand block */
  .brand {
    position: absolute;
    left: 82px;
    top: 98px;
    width: 224px;
    display: flex;
    flex-direction: column;
    align-items: center;
  }
  .brand__square {
    width: 130px;
    height: 130px;
    background: var(--mark-grey);
  }
  .brand__name {
    margin-top: 40px;
    font-size: 17px;
    font-weight: 400;
    letter-spacing: 1.2px;
    text-transform: uppercase;
    color: var(--ink-soft);
    white-space: nowrap;
  }

  .divider {
    position: absolute;
    left: 340px;
    top: 94px;
    width: 2px;
    height: 216px;
    background: var(--rule);
  }

  /* front: contact details */
  .details {
    position: absolute;
    left: 364px;
    top: 86px;
    color: var(--ink-soft);
  }
  .details__name {
    font-size: 27px;
    font-weight: 700;
    color: var(--ink);
    line-height: 1.1;
  }
  .details__role {
    font-size: 18px;
    line-height: 1.3;
  }
  .contact-list {
    list-style: none;
    margin-top: 26px;
  }
  .contact-list li {
    display: flex;
    align-items: center;
    font-size: 22px;
    line-height: 26px;
  }
  .contact-list svg {
    width: 16px;
    height: 16px;
    margin-right: 8px;
    fill: var(--ink);
  }
  .address {
    margin-top: 14px;
    font-size: 19px;
    line-height: 23px;
    font-style: normal;
  }

  /* back */
  .back-brand {
    position: absolute;
    inset: 0;
    display: flex;
    flex-direction: column;
    align-items: center;
    padding-top: 64px;
  }
  .back-brand__square {
    width: 170px;
    height: 170px;
    background: var(--mark-grey);
  }
  .back-brand__name {
    margin-top: 64px;
    font-size: 30px;
    font-weight: 400;
    letter-spacing: 2px;
    text-transform: uppercase;
    color: var(--mark-light);
    white-space: nowrap;
  }
</style>
</head>
<body>
<main class="canvas">

  <section class="card card--front" aria-label="Business card front">
    <div class="brand">
      <div class="brand__square"></div>
      <p class="brand__name">Walsh &amp; Brand Pty Ltd.</p>
    </div>

    <div class="divider"></div>

    <div class="details">
      <h1 class="details__name">Owen Walsh</h1>
      <p class="details__role">Sales Agents</p>

      <ul class="contact-list">
        <li>
          <svg viewBox="0 0 16 16" aria-hidden="true"><path d="M4 1h8a1.5 1.5 0 0 1 1.5 1.5v11A1.5 1.5 0 0 1 12 15H4a1.5 1.5 0 0 1-1.5-1.5v-11A1.5 1.5 0 0 1 4 1zm0.5 2v9.5h7V3z"/></svg>
          0431 857 219
        </li>
        <li>
          <svg viewBox="0 0 16 16" aria-hidden="true"><path d="M1 6c0-2 3-3.5 7-3.5S15 4 15 6v1.5h-3.5V6h-7v1.5H1z"/><path d="M4.5 8h7l2 6h-11z"/></svg>
          07 5948 2063
        </li>
        <li>
          <svg viewBox="0 0 16 16" aria-hidden="true"><path d="M4 1h8v4H4z"/><path d="M1 6h14v6h-3v3H4v-3H1zm4 4v3h6v-3z"/></svg>
          07 5948 2174
        </li>
      </ul>

      <address class="address">
        3/42 Marlow Crescent<br>
        FERNLEA QLD 4213
      </address>
    </div>
  </section>

  <section class="card card--back" aria-label="Business card back">
    <div class="back-brand">
      <div class="back-brand__square"></div>
      <p class="back-brand__name">Walsh &amp; Brand Pty Ltd.</p>
    </div>
  </section>

</main>
</body>
</html>
```